Tech business card design

We need an amazing business card design for our new business 'Pexla' a marketing tech startup based in Sydney, Australia. We provide an online marketplace for businesses to search and buy advertising media, connect with service providers and learn more about marketing. We wish to communicate 'cool tech', reliability and professionalism and design based around our logo.

Target Market(s)

Business Owners

Contact Information for Business Card

Name
Position
Email Address
Website
Phone Number

Font styles to use
Other font styles liked:
• Avenir & Avenir Next

Colors

Designer to choose colors to be used in the design.

```html
<!DOCTYPE html>
<html lang="en">
<head>
<meta charset="utf-8">
<title>Pexla Business Card</title>
<link href="https://fonts.googleapis.com/css2?family=Nunito+Sans:wght@400;600;800&display=swap" rel="stylesheet">
<style>
  :root {
    --navy: #12143a;
    --teal: #6ab0be;
    --teal-light: #8cc3cf;
    --ink: #3a3a44;
    --paper: #ffffff;
    --backdrop: #efefef;
  }
  * { margin: 0; padding: 0; box-sizing: border-box; }
  html, body {
    width: 1200px; height: 900px; overflow: hidden;
    background: var(--backdrop);
    font-family: "Nunito Sans", "Avenir Next", Avenir, sans-serif;
  }
  .card {
    position: absolute; left: 302px; width: 596px; height: 340px;
    overflow: hidden;
  }
  .card-front { top: 85px; background: var(--navy); }
  .card-back { top: 475px; background: var(--paper); }

  .front-art { position: absolute; inset: 0; }

  .front-brand {
    position: absolute; left: 358px; top: 118px;
    color: var(--paper);
  }
  .wordmark {
    font-weight: 800; font-size: 72px; line-height: 1;
    letter-spacing: -1px;
  }
  .front-url {
    color: var(--teal); font-size: 16px; letter-spacing: 0.3px;
    margin-top: 4px;
  }

  .back-wordmark {
    position: absolute; left: 55px; top: 128px;
    color: var(--navy);
  }

  .contact-block { position: absolute; left: 334px; top: 100px; }
  .person-name {
    font-size: 21px; font-weight: 600; letter-spacing: 0.5px;
    color: var(--navy); line-height: 1;
  }
  .person-name .surname { color: var(--teal); }
  .person-role {
    display: inline-block; margin-top: 5px; width: 163px;
    padding: 2px 0 2px 3px;
    background: linear-gradient(90deg, var(--navy) 0%, var(--navy) 25%, var(--teal) 100%);
    color: var(--paper); font-size: 15px; line-height: 21px;
  }
  .contact-list { list-style: none; margin-top: 10px; }
  .contact-list li {
    display: flex; align-items: center; gap: 9px;
    height: 25px; font-size: 16px; color: var(--ink);
  }
  .contact-list svg { width: 16px; height: 16px; flex: none; }

  .card-band {
    position: absolute; left: 0; right: 0; bottom: 0; height: 11px;
    background: linear-gradient(90deg, var(--navy) 0%, var(--navy) 30%, var(--teal) 65%, var(--teal) 100%);
  }
</style>
</head>
<body>

<section class="card card-front">
  <svg class="front-art" viewBox="0 0 596 340" width="596" height="340">
    <defs>
      <linearGradient id="photoTone" x1="0" y1="0" x2="1" y2="1">
        <stop offset="0" stop-color="#7fbcc9"/>
        <stop offset="0.6" stop-color="#5a9fb0"/>
        <stop offset="1" stop-color="#3f7f93"/>
      </linearGradient>
    </defs>
    <path d="M0 0 H80 L318 140 Q338 165 318 190 L82 340 H0 Z" fill="var(--paper)"/>
    <path role="img" aria-label="Photo of business people reviewing charts on a tablet and laptop" d="M0 0 H58 L300 142 Q318 165 300 188 L62 340 H0 Z" fill="url(#photoTone)"/>
  </svg>
  <div class="front-brand">
    <div class="wordmark">pexla</div>
    <div class="front-url">www.pexlamedia.com.au</div>
  </div>
</section>

<section class="card card-back">
  <div class="back-wordmark wordmark">pexla</div>

  <div class="contact-block">
    <div class="person-name">DANIEL <span class="surname">ROSS</span></div>
    <div class="person-role">Founder | Director</div>
    <ul class="contact-list">
      <li>
        <svg viewBox="0 0 16 16"><rect x="4" y="1" width="8" height="14" rx="1.5" fill="none" stroke="var(--navy)" stroke-width="1.6"/><circle cx="8" cy="12.5" r="0.9" fill="var(--navy)"/></svg>
        <span>+61 (0)400 555 218</span>
      </li>
      <li>
        <svg viewBox="0 0 16 16"><rect x="1" y="3.5" width="14" height="9.5" fill="var(--navy)"/><path d="M1.5 4 L8 9 L14.5 4" fill="none" stroke="var(--paper)" stroke-width="1.2"/></svg>
        <span>daniel@pexlamedia.com.au</span>
      </li>
      <li>
        <svg viewBox="0 0 16 16"><circle cx="8" cy="8" r="7" fill="var(--navy)"/><path d="M4 4 Q7 5 6 8 Q9 9 8 13 M10 3 Q11 6 13 7" fill="none" stroke="var(--paper)" stroke-width="1.3"/></svg>
        <span>www.pexlamedia.com.au</span>
      </li>
    </ul>
  </div>

  <div class="card-band"></div>
</section>

</body>
</html>
```